KRT Project Signage

Need a sign to be displayed in the front of properties currently under Construction or Renovation to advertise our company information. Need it to be Professional and Contemporary. We are a Design/Build Construction Company. Information should include Company Name, email, website, phone number. Attached: Logo and company brochure, also included and inspiration images

```html
<!DOCTYPE html>
<html lang="en">
<head>
<meta charset="utf-8">
<title>KRT Construction – Project Sign</title>
<link href="https://fonts.googleapis.com/css2?family=Abhaya+Libre:wght@400;600;800&display=swap" rel="stylesheet">
<style>
  :root {
    --backdrop: #e5e5e5;
    --paper: #ffffff;
    --signal-yellow: #f2e941;
    --ink: #0d0d0d;
    --reverse: #ffffff;
  }
  * { margin: 0; padding: 0; box-sizing: border-box; }
  html, body {
    width: 1004px; height: 1200px; overflow: hidden;
    background: var(--backdrop);
    font-family: "Abhaya Libre", Georgia, serif;
  }
  .sign {
    position: absolute; left: 67px; top: 84px;
    width: 829px; height: 1036px;
    display: flex; flex-direction: column;
  }
  .brand-panel {
    height: 479px; background: var(--paper);
    display: flex; flex-direction: column; justify-content: center; align-items: center;
    gap: 14px; padding-bottom: 40px;
  }
  .brand-name {
    font-weight: 800; font-size: 74px; letter-spacing: 3px;
    color: var(--ink); line-height: 1;
    display: flex; align-items: center; gap: 18px;
  }
  .brand-dot {
    width: 34px; height: 34px; border-radius: 50%;
    background: var(--signal-yellow);
  }
  .brand-tagline {
    font-weight: 600; font-size: 34px; letter-spacing: 4px;
    color: var(--ink);
  }
  .services-band {
    height: 364px; background: var(--signal-yellow);
    text-align: center; color: var(--ink);
    padding-top: 36px;
  }
  .services-headline {
    font-weight: 800; font-size: 52px; line-height: 74px;
    text-transform: uppercase;
  }
  .services-list {
    margin-top: 18px;
    font-weight: 400; font-size: 48px; line-height: 64px;
  }
  .contact-bar {
    height: 193px; background: var(--ink); color: var(--reverse);
    text-align: center; font-weight: 600; font-size: 30px; line-height: 51px;
    padding-top: 20px;
  }
</style>
</head>
<body>
  <main class="sign">
    <section class="brand-panel">
      <h1 class="brand-name"><span class="brand-dot"></span>KRT CONSTRUCTION</h1>
      <p class="brand-tagline">LUXURY RENOVATIONS</p>
    </section>
    <section class="services-band">
      <h2 class="services-headline">We are a design/build<br>construction company</h2>
      <p class="services-list">•remodeling •interior design<br>•new home construction</p>
    </section>
    <footer class="contact-bar">
      <p>1840 NW 4th Ave., Ste. 310 Boca Raton, FL 33431</p>
      <p>Direct 561.555.0142 Office 561.555.0198</p>
      <p>marc@krtconstruction.com</p>
    </footer>
  </main>
</body>
</html>
```